Business Card Design

I already have a company logo for my company. I have a logo for the manufacturer we represent. I want a professional business card design.

```html
<!DOCTYPE html>
<html lang="en">
<head>
<meta charset="utf-8">
<title>Beacon Roadworks LLC – Business Card</title>
<link rel="stylesheet" href="https://fonts.googleapis.com/css2?family=Open+Sans:wght@400;600;700;800&display=swap">
<style>
  :root {
    --stage: #232323;
    --card-white: #ffffff;
    --brand-red: #e3202a;
    --brand-gold: #b8922e;
    --ink: #1c1c1c;
    --green-deep: #0f2d17;
    --green-mid: #1c5a2c;
    --green-light: #2a7a3d;
  }
  * { box-sizing: border-box; margin: 0; padding: 0; }
  html, body {
    width: 1200px;
    height: 780px;
    overflow: hidden;
    background: var(--stage);
    font-family: "Open Sans", Arial, sans-serif;
  }
  .stage {
    position: relative;
    width: 1200px;
    height: 780px;
    display: flex;
    align-items: center;
    justify-content: center;
    gap: 40px;
  }
  .card {
    position: relative;
    width: 520px;
    height: 298px;
    overflow: hidden;
    box-shadow: 0 14px 30px rgba(0, 0, 0, 0.45);
  }

  /* Front */
  .card-front { background: var(--card-white); }
  .edge-band {
    position: absolute;
    width: 9px;
    background: var(--brand-red);
  }
  .edge-band--left { left: 0; top: 44px; height: 118px; }
  .edge-band--right { right: 0; top: 190px; height: 108px; }

  .brand {
    position: absolute;
    left: 58px;
    top: 62px;
    display: flex;
    align-items: center;
    gap: 10px;
  }
  .brand-mark {
    width: 26px;
    height: 26px;
    background: var(--brand-red);
  }
  .brand-name {
    font-weight: 800;
    font-size: 19px;
    line-height: 1.15;
    color: var(--brand-red);
    letter-spacing: 0.5px;
  }

  .divider {
    position: absolute;
    left: 250px;
    top: 60px;
    width: 1.5px;
    height: 150px;
    background: var(--brand-gold);
    transform: rotate(38deg);
    transform-origin: center;
  }

  .person {
    position: absolute;
    left: 300px;
    top: 92px;
  }
  .person-name {
    font-weight: 800;
    font-size: 27px;
    line-height: 1.1;
    color: var(--brand-red);
  }
  .person-name .surname { color: var(--brand-gold); }
  .person-role {
    font-weight: 600;
    font-size: 12.5px;
    color: var(--ink);
    margin-top: 2px;
  }
  .contact-list {
    list-style: none;
    margin-top: 16px;
    font-size: 12.5px;
    color: var(--ink);
  }
  .contact-list li {
    display: flex;
    align-items: center;
    gap: 7px;
    line-height: 19px;
  }
  .contact-list svg { width: 11px; height: 11px; flex: none; }

  .address {
    position: absolute;
    left: 40px;
    bottom: 36px;
    font-size: 12.5px;
    color: var(--ink);
  }

  /* Back */
  .card-back {
    display: flex;
    align-items: center;
    justify-content: center;
  }
  .back-texture {
    position: absolute;
    inset: 0;
    background: radial-gradient(ellipse at 55% 45%, var(--green-mid) 0%, var(--green-deep) 60%, var(--green-light) 100%);
  }
  .brand--back {
    position: relative;
    left: auto;
    top: auto;
  }
  .brand--back .brand-name { font-size: 24px; }
  .brand--back .brand-mark { width: 32px; height: 32px; }
</style>
</head>
<body>
<main class="stage">

  <section class="card card-front" aria-label="Business card front">
    <div class="edge-band edge-band--left"></div>
    <div class="edge-band edge-band--right"></div>

    <div class="brand">
      <span class="brand-mark"></span>
      <span class="brand-name">BEACON<br>ROADWORKS LLC</span>
    </div>

    <div class="divider"></div>

    <div class="person">
      <h1 class="person-name">Daniel <span class="surname">Varga</span></h1>
      <p class="person-role">Managing Director</p>
      <ul class="contact-list">
        <li>
          <svg viewBox="0 0 12 12" aria-hidden="true"><path d="M2.5 1h2l1 3-1.3 1a6 6 0 0 0 2.8 2.8l1-1.3 3 1v2a1 1 0 0 1-1 1A9.5 9.5 0 0 1 1.5 2a1 1 0 0 1 1-1z" fill="var(--brand-red)"/></svg>
          (555) 014-2290
        </li>
        <li>
          <svg viewBox="0 0 12 12" aria-hidden="true"><rect x="1" y="2.5" width="10" height="7" rx="1" fill="var(--brand-red)"/><path d="M1.5 3l4.5 3.5L10.5 3" stroke="#fff" stroke-width="1" fill="none"/></svg>
          info@beaconroadworks.com
        </li>
        <li>
          <svg viewBox="0 0 12 12" aria-hidden="true"><circle cx="6" cy="6" r="5" fill="var(--brand-red)"/><path d="M1 6h10M6 1c-2 2.5-2 7.5 0 10M6 1c2 2.5 2 7.5 0 10" stroke="#fff" stroke-width="0.8" fill="none"/></svg>
          www.beaconroadworks.com
        </li>
      </ul>
    </div>

    <p class="address">418 Harbor Line Ave Millbrook, Texas 75000 USA</p>
  </section>

  <section class="card card-back" aria-label="Business card back">
    <div class="back-texture" role="img" aria-label="Green background with fine diagonal stripe texture"></div>
    <div class="brand brand--back">
      <span class="brand-mark"></span>
      <span class="brand-name">BEACON<br>ROADWORKS LLC</span>
    </div>
  </section>

</main>
</body>
</html>
```